Distribution company for alcoholic beverages called Amber Crestline needs a web design

1. We would like to first page to show

A. The company logo (in att)

B. A wall of bottles similar to
- www.underpaperskies.com that will click through to the brand info
- https://keltaronworks.com/brands/
PLEASE NOTE THAT IT CAN NOT BE THE SAME DESIGN - it needs to have a different look and feel ... this is to show what we mean with a wall of bottles

Important = we need to be able to keep adding new bottles/brands over time

C. only 3 tabs needed – Brands, About Us and Contact

Style
- simple and clean
- colourful
- classy

2. Page 2
The intro page to describe the company
we can use the same (Box + drop) logo to create a visual

3. Page 3
The referral page to the specific brands/company
= we need to alternating versions of this / just different ordering in the page

Target Market(s)

importers, brand owners, bartenders,

Industry/Entity Type

It Company

Number of Pages Required

3 page

Requirements
Must have
• A landing page visual that can display bottles we will sell in an organised way
• We need to be able to add bottles when the portfolio expands
Nice to have
• to have the drop out of the logo as a part of the design of the website

```html
<!DOCTYPE html>
<html lang="en">
<head>
<meta charset="utf-8">
<title>Amber Crestline — About Us</title>
<link rel="stylesheet" href="https://fonts.googleapis.com/css2?family=Roboto:wght@400;500&display=swap">
<style>
  :root {
    --ink: #111111;
    --paper: #ffffff;
    --footer-bg: #000000;
    --nav-text: #ffffff;
    --barrel-dark: #1e130b;
    --barrel-mid: #5a3e25;
    --barrel-light: #8a6740;
  }
  * { margin: 0; padding: 0; box-sizing: border-box; }
  html, body {
    width: 1200px;
    height: 1145px;
    overflow: hidden;
    background: var(--paper);
    font-family: "Roboto", Arial, sans-serif;
    color: var(--ink);
  }
  .page { position: relative; width: 1200px; height: 1145px; }

  .hero {
    position: absolute; left: 0; top: 0;
    width: 1200px; height: 562px;
    background:
      radial-gradient(ellipse at 50% 50%, rgba(138,103,64,0.55) 0%, rgba(30,19,11,0) 70%),
      linear-gradient(180deg, var(--barrel-mid) 0%, var(--barrel-light) 45%, var(--barrel-mid) 75%, var(--barrel-dark) 100%);
  }

  .site-header {
    position: absolute; left: 0; top: 0; width: 1200px; height: 100px;
  }
  .brand-name {
    position: absolute; left: 213px; top: 44px;
    font-weight: 500; font-size: 17px; letter-spacing: 1.5px;
    color: var(--nav-text); white-space: nowrap;
  }
  .main-nav, .footer-nav { position: absolute; left: 0; top: 0; width: 1200px; }
  .nav-link {
    position: absolute;
    transform: translateX(-50%);
    font-size: 10.5px; font-weight: 500; letter-spacing: 0.6px;
    color: var(--nav-text); text-decoration: none; white-space: nowrap;
  }
  .nav-link.is-active {
    border: 1px solid var(--nav-text);
    width: 88px; height: 28px; line-height: 26px; text-align: center;
  }

  .about-copy {
    position: absolute; left: 272px; top: 656px; width: 660px;
    font-size: 12px; line-height: 21.9px; letter-spacing: 0.9px;
  }
  .about-copy p { text-indent: 28px; }

  .closing-line {
    position: absolute; left: 0; width: 1200px; text-align: center;
    font-size: 15px; letter-spacing: 1.2px;
  }
  .closing-line.invite { top: 903px; }
  .closing-line.motto { top: 944px; }

  .site-footer {
    position: absolute; left: 0; top: 1051px;
    width: 1200px; height: 94px; background: var(--footer-bg);
  }
  .site-footer .brand-name { left: 213px; top: 38px; font-size: 12px; letter-spacing: 1px; }
</style>
</head>
<body>
<div class="page">
  <div class="hero" role="img" aria-label="Photograph of rows of oak whisky barrels stacked on wooden racks in a dark warehouse"></div>

  <header class="site-header">
    <div class="brand-name">AMBER CRESTLINE</div>
    <nav class="main-nav">
      <a class="nav-link" href="#" style="left:650px; top:50px;">HOME</a>
      <a class="nav-link" href="#" style="left:755px; top:50px;">BRANDS</a>
      <a class="nav-link is-active" href="#" style="left:859px; top:42px;">ABOUT US</a>
      <a class="nav-link" href="#" style="left:962px; top:50px;">CONTACT</a>
    </nav>
  </header>

  <main>
    <section class="about-copy">
      <p>Amber Crestline started with one thought “wouldn’t it be nice for smaller local brands have a real global outreach?”. Brands made by people who cared, who wanted to bring the world different perspectives and tastes.</p>
      <p>While more craft brands keep popping up we noticed many of them can use a hand when it comes to creating and excecuting an export strategy. From understanding legislation, international pricing to finding the right distributor partner.</p>
      <p>The world is a big place, therefeore we offer vast export expertise with an over 90 market network, which can take shape in just setting up your international market, or moreover is also able to support your export markets by,&nbsp; putting together marketing plans and visits by our own brandambassador support team.</p>
    </section>
    <p class="closing-line invite">If you are interested to learn more just let us know.</p>
    <p class="closing-line motto">Let us prove (y)our strength!</p>
  </main>

  <footer class="site-footer">
    <div class="brand-name">AMBER CRESTLINE</div>
    <nav class="footer-nav">
      <a class="nav-link" href="#" style="left:647px; top:40px;">HOME</a>
      <a class="nav-link" href="#" style="left:752px; top:40px;">BRANDS</a>
      <a class="nav-link is-active" href="#" style="left:856px; top:32px;">ABOUT US</a>
      <a class="nav-link" href="#" style="left:961px; top:40px;">CONTACT</a>
    </nav>
  </footer>
</div>
</body>
</html>
```